Spiritual Healing bussiness needs logo/business card

Simple, clean looking logo/card
For spiritual business with healing services and occult rituals

Contact Information for Business Card

Needs my name: Tobin Varley
Business name: Lantern Healing Shop
Services provided and worded in this way:

Reiki Healing
Tarot
Oils
Rituals Of Change

Can look occult like but with light energy.

Colors
0255a3
3276b5
85abd2
33a6d7
85cae6
0292cd

```html
<!DOCTYPE html>
<html lang="en">
<head>
<meta charset="utf-8">
<title>Lantern Healing Shop – Business Card</title>
<link href="https://fonts.googleapis.com/css2?family=Roboto+Slab:wght@400;500&family=Lato:wght@400&display=swap" rel="stylesheet">
<style>
  :root {
    --navy: #0255a3;
    --mid-blue: #3276b5;
    --sky: #0292cd;
    --sky-light: #33a6d7;
    --pale: #85cae6;
    --backdrop: #6b6b6b;
    --paper: #ffffff;
    --rule: #9a9a9a;
    --ink-dark: #3a3a3a;
  }
  * { margin: 0; padding: 0; box-sizing: border-box; }
  html, body { width: 1200px; height: 802px; overflow: hidden; }
  body { background: var(--backdrop); position: relative; font-family: 'Lato', sans-serif; }

  .card {
    position: absolute;
    top: 274px;
    width: 442px;
    height: 265px;
    overflow: hidden;
    box-shadow: 2px 3px 6px rgba(0,0,0,0.45);
  }
  .card--front { left: 136px; background: var(--paper); }
  .card--back { left: 624px; background: var(--sky); }

  /* Front */
  .brand {
    position: absolute;
    left: 12px;
    top: 82px;
    width: 200px;
    text-align: center;
  }
  .brand__disc {
    display: block;
    margin: 0 auto;
    width: 78px;
    height: 78px;
    border-radius: 50%;
    border: 6px solid var(--navy);
  }
  .brand__name {
    margin-top: 8px;
    font-family: 'Roboto Slab', serif;
    font-weight: 500;
    font-size: 16px;
    color: var(--navy);
    white-space: nowrap;
  }
  .divider {
    position: absolute;
    left: 222px;
    top: 84px;
    width: 1px;
    height: 97px;
    background: var(--rule);
  }
  .person {
    position: absolute;
    left: 234px;
    top: 82px;
    font-family: 'Roboto Slab', serif;
    font-size: 17px;
    color: var(--navy);
  }
  .person__last { color: var(--sky); }
  .contacts {
    position: absolute;
    left: 234px;
    top: 128px;
    list-style: none;
    font-size: 12.5px;
    color: var(--ink-dark);
    line-height: 17px;
  }
  .contacts li { display: flex; align-items: center; gap: 3px; }
  .contacts svg { width: 14px; height: 14px; flex: none; }

  .services {
    position: absolute;
    left: 0; bottom: 0;
    width: 100%;
    height: 46px;
    background: var(--sky);
    color: var(--paper);
    font-size: 12.5px;
    display: flex;
    align-items: center;
    justify-content: center;
    padding-right: 6px;
    gap: 10px;
  }
  .services__dot { width: 5px; height: 5px; border-radius: 50%; background: var(--paper); }

  /* Back */
  .back-field {
    position: absolute;
    inset: 0;
    background: linear-gradient(180deg, #1c9fd6 0%, var(--sky) 100%);
  }
  .back-name {
    position: absolute;
    left: 0; right: 0;
    top: 121px;
    text-align: center;
    font-family: 'Roboto Slab', serif;
    font-weight: 500;
    font-size: 18px;
    color: var(--paper);
  }
</style>
</head>
<body>

<section class="card card--front">
  <div class="brand">
    <span class="brand__disc"></span>
    <p class="brand__name">Lantern Healing Shop</p>
  </div>

  <div class="divider"></div>

  <h1 class="person">Tobin <span class="person__last">Varley</span></h1>

  <ul class="contacts">
    <li>
      <svg viewBox="0 0 14 14"><circle cx="7" cy="7" r="6.3" fill="none" stroke="var(--navy)" stroke-width="1.2"/><path d="M3.6 8.6h6.8v1.6H3.6zM4.2 8.4l1-2.4h3.6l1 2.4zM3.4 5.4c1.6-1.4 5.6-1.4 7.2 0v1H3.4z" fill="var(--navy)"/></svg>
      044-555 210 384
    </li>
    <li>
      <svg viewBox="0 0 14 14"><circle cx="7" cy="7" r="6.3" fill="none" stroke="var(--navy)" stroke-width="1.2"/><rect x="3.5" y="4.5" width="7" height="5" fill="var(--navy)"/><path d="M3.5 4.8L7 7.4l3.5-2.6" fill="none" stroke="#fff" stroke-width="0.8"/></svg>
      hello@lanternhealing.com
    </li>
    <li>
      <svg viewBox="0 0 14 14"><circle cx="7" cy="7" r="6.3" fill="none" stroke="var(--navy)" stroke-width="1.2"/><circle cx="7" cy="7" r="3.8" fill="var(--navy)"/></svg>
      www.LanternHealingShop.com
    </li>
  </ul>

  <div class="services">
    <span>Reiki Healing</span><span class="services__dot"></span>
    <span>Tarot</span><span class="services__dot"></span>
    <span>Oils</span><span class="services__dot"></span>
    <span>Rituals Of Change</span>
  </div>
</section>

<section class="card card--back">
  <div class="back-field" role="img" aria-label="Repeating pattern of the brand mark in lighter blue tones across the card"></div>
  <p class="back-name">Lantern Healing Shop</p>
</section>

</body>
</html>
```